KRT Project Signage

Need a sign to be displayed in the front of properties currently under Construction or Renovation to advertise our company information. Need it to be Professional and Contemporary. We are a Design/Build Construction Company. Information should include Company Name, email, website, phone number. Attached: Logo and company brochure, also included and inspiration images

```html
<!DOCTYPE html>
<html lang="en">
<head>
<meta charset="utf-8">
<title>KRT Construction – Project Sign</title>
<link rel="stylesheet" href="https://fonts.googleapis.com/css2?family=Poppins:wght@500;600;700&display=swap">
<style>
  :root {
    --bg: #f4f4f4;
    --sign-white: #ffffff;
    --sign-black: #0d0d0d;
    --ink: #111111;
    --accent: #ece82f;
    --icon-grey: #bdbdbd;
    --text-light: #ffffff;
  }
  * { margin: 0; padding: 0; box-sizing: border-box; }
  html, body { width: 1200px; height: 3455px; overflow: hidden; }
  body {
    background: var(--bg);
    font-family: "Poppins", Arial, sans-serif;
    position: relative;
  }
  .sign {
    position: absolute;
    left: 60px;
    top: 917px;
    width: 1080px;
    height: 1620px;
    background: var(--sign-white);
    box-shadow: 0 18px 50px rgba(0,0,0,0.35);
  }
  .sign__body {
    position: absolute;
    left: 0; top: 561px;
    width: 100%; height: 884px;
    background: var(--sign-black);
  }
  .brand {
    position: absolute;
    left: 0; top: 150px; width: 100%;
    text-align: center;
    color: var(--ink);
  }
  .brand__name {
    display: inline-flex;
    align-items: center;
    gap: 22px;
    font-weight: 600;
    font-size: 66px;
    letter-spacing: 3px;
    line-height: 1;
  }
  .brand__dot {
    width: 46px; height: 46px;
    border-radius: 50%;
    background: var(--accent);
  }
  .brand__rule {
    width: 700px; height: 5px;
    margin: 22px auto 0;
    background: var(--accent);
  }
  .brand__tagline {
    margin-top: 16px;
    font-weight: 500;
    font-size: 38px;
    letter-spacing: 4px;
  }
  .brand__web {
    margin-top: 14px;
    font-weight: 600;
    font-size: 32px;
  }
  .phone-pill {
    position: absolute;
    left: 79px; top: 506px;
    width: 920px; height: 156px;
    background: var(--sign-black);
    border: 5px solid var(--sign-white);
    border-radius: 78px;
    display: flex; align-items: center; justify-content: center;
    gap: 28px;
    padding: 0 40px;
    color: var(--text-light);
    font-weight: 700;
    font-size: 104px;
    letter-spacing: 0;
    line-height: 1;
    white-space: nowrap;
  }
  .phone-pill svg { width: 76px; height: 76px; flex: none; }
  .phone-pill__number { padding-top: 8px; }
  .contact {
    position: absolute; left: 0; width: 100%;
    text-align: center;
    color: var(--text-light);
    font-weight: 600;
    line-height: 1;
  }
  .contact-icon {
    position: absolute; left: 50%;
    transform: translateX(-50%);
  }
  .contact--fax { top: 795px; font-size: 76px; font-weight: 700; letter-spacing: 2px; }
  .contact--email { top: 1015px; font-size: 56px; font-weight: 500; }
  .contact--address { top: 1205px; font-size: 50px; line-height: 63px; }
  .sign__footer {
    position: absolute; left: 0; top: 1445px;
    width: 100%; height: 175px;
    display: flex; align-items: center; justify-content: center;
    color: var(--ink);
    font-weight: 700;
    font-size: 66px;
  }
</style>
</head>
<body>
  <div class="sign">
    <div class="sign__body"></div>

    <div class="brand">
      <div class="brand__name"><span class="brand__dot"></span>KRT CONSTRUCTION</div>
      <div class="brand__rule"></div>
      <div class="brand__tagline">LUXURY RENOVATIONS</div>
      <div class="brand__web">www.krtconstruction.com</div>
    </div>

    <div class="phone-pill">
      <svg viewBox="0 0 64 64" aria-hidden="true">
        <path fill="#ece82f" d="M18 6c3 0 5 7 6 10s-2 5-4 7c2 6 8 13 15 16 2-2 4-5 7-4s10 4 10 7-4 10-9 10C25 52 8 34 6 15 6 10 14 6 18 6z"/>
        <path fill="none" stroke="#ece82f" stroke-width="4" stroke-linecap="round" d="M36 14a14 14 0 0 1 14 14M36 4a24 24 0 0 1 24 24"/>
      </svg>
      <span class="phone-pill__number">555.318.4027</span>
    </div>

    <svg class="contact-icon" style="top:691px" width="70" height="82" viewBox="0 0 70 82" aria-hidden="true">
      <rect x="22" y="2" width="34" height="22" fill="none" stroke="#bdbdbd" stroke-width="4"/>
      <rect x="2" y="26" width="14" height="54" rx="4" fill="#bdbdbd"/>
      <rect x="19" y="26" width="49" height="54" rx="4" fill="#bdbdbd"/>
      <g fill="#0d0d0d">
        <rect x="26" y="33" width="35" height="9"/>
        <rect x="26" y="48" width="7" height="6"/><rect x="40" y="48" width="7" height="6"/><rect x="54" y="48" width="7" height="6"/>
        <rect x="26" y="60" width="7" height="6"/><rect x="40" y="60" width="7" height="6"/><rect x="54" y="60" width="7" height="6"/>
      </g>
    </svg>
    <div class="contact contact--fax">555.318.4090</div>

    <svg class="contact-icon" style="top:925px" width="72" height="66" viewBox="0 0 72 66" aria-hidden="true">
      <path fill="#bdbdbd" d="M2 28 36 4l34 24v36H2z"/>
      <rect x="14" y="10" width="44" height="34" fill="#0d0d0d"/>
      <text x="36" y="34" text-anchor="middle" font-family="Poppins, sans-serif" font-size="22" fill="#bdbdbd">@</text>
      <path fill="none" stroke="#0d0d0d" stroke-width="3" d="M2 28l34 22 34-22M2 64l26-20M70 64 44 44"/>
    </svg>
    <div class="contact contact--email">info@krtconstruction.com</div>

    <svg class="contact-icon" style="top:1112px" width="74" height="76" viewBox="0 0 74 76" aria-hidden="true">
      <ellipse cx="37" cy="62" rx="32" ry="11" fill="none" stroke="#bdbdbd" stroke-width="5"/>
      <path fill="#bdbdbd" d="M37 68C30 56 16 40 16 24a21 21 0 0 1 42 0c0 16-14 32-21 44z"/>
      <circle cx="37" cy="24" r="8" fill="#0d0d0d"/>
    </svg>
    <div class="contact contact--address">1480 Harbor View Rd.<br>Suite 305<br>Palm Cove, FL 30417</div>

    <div class="sign__footer">www.krtconstruction.com</div>
  </div>
</body>
</html>
```